Logo & Visitenkarte für Weinbauer
Zielgruppe
Ich bin Weinbauer und betreibe auch einen Buschenschank. Zielgruppe ist die Gastronomie und der (Durchschnitts-) Endverbraucher.
Aufgabenstellung
Unsere Betriebsstätte ist im Rebhügelgau Weinviertel (Österreich).
Wir wollen die Werte Tradition, Regional, Vertrauen und Bodenständigkeit vermitteln.
Unsere Kunden schätzen die Herkunft.
Das Logo soll als Firmenlogo und auch für die Weinetiketten verwendet werden können.

```html
<!DOCTYPE html>
<html lang="de">
<head>
<meta charset="utf-8">
<title>Weinbau Lindauer – Etikett</title>
<link rel="stylesheet" href="https://fonts.googleapis.com/css2?family=Raleway:wght@400;600&display=swap">
<style>
  :root {
    --backdrop: #d9d9d9;
    --label-red: #5a1c1f;
    --label-red-light: #6b2528;
    --gold: #b98a5e;
    --gold-soft: #c9a27c;
  }
  html, body {
    margin: 0;
    padding: 0;
    width: 1200px;
    height: 960px;
    overflow: hidden;
    background: var(--backdrop);
  }
  .canvas {
    position: relative;
    width: 1200px;
    height: 960px;
    display: flex;
    align-items: center;
    justify-content: center;
  }
  .wine-label {
    width: 760px;
    height: 340px;
    background: linear-gradient(90deg, var(--label-red) 0%, var(--label-red-light) 50%, var(--label-red) 100%);
    display: flex;
    flex-direction: column;
    align-items: center;
    justify-content: center;
    gap: 22px;
    box-sizing: border-box;
    padding: 36px 80px;
  }
  .brand {
    display: flex;
    align-items: center;
    gap: 18px;
  }
  .brand-dot {
    width: 64px;
    height: 64px;
    border-radius: 50%;
    background: var(--gold);
    flex: none;
  }
  .brand-name {
    font-family: "Raleway", sans-serif;
    font-weight: 600;
    font-size: 46px;
    letter-spacing: 0.06em;
    text-transform: uppercase;
    color: var(--gold);
    margin: 0;
  }
  .label-copy {
    font-family: "Raleway", sans-serif;
    font-weight: 400;
    font-size: 13px;
    line-height: 1.6;
    color: var(--gold-soft);
    text-align: center;
    max-width: 460px;
    margin: 0;
  }
</style>
</head>
<body>
  <main class="canvas">
    <section class="wine-label">
      <div class="brand">
        <span class="brand-dot" aria-hidden="true"></span>
        <h1 class="brand-name">Weinbau Lindauer</h1>
      </div>
      <p class="label-copy">Grüner Veltliner aus dem Rebhügelgau. Handgelesen, schonend gekeltert und im Keller gereift. Frisch, würzig und mit feiner Frucht – ein ehrlicher Wein vom Familienbetrieb.</p>
    </section>
  </main>
</body>
</html>
```